Corporate web site design for a blockchain oriented company

Design a web site for Velmora. The company works on blockchain projects, mostly in B2B . Logo and content of the web site are attached with the project.

Corporate web sites means that we need to present the company and, at least, two of its projects.

Target Market(s)

B2B (Telecom, Gvt, online e-commerce web sites, banks, insurance ...)

Number of Pages Required

3 page

Font styles to use
Sans Serif

Requirements
Must have
• Landing page
• Page for KYC product
• Page for Loyalty product
• Team presentation
• Contact form
• Company presentation
• Several section can be in one page.
Nice to have
• Teaser video per project.
Should not have
• Heavy web site with a lot of animations.

```html
<!DOCTYPE html>
<html lang="en">
<head>
<meta charset="utf-8">
<title>Velmora — Blockchain solutions provider</title>
<link href="https://fonts.googleapis.com/css2?family=Roboto+Condensed:wght@400;700&family=Open+Sans:wght@400;600&display=swap" rel="stylesheet">
<style>
:root{
  --purple:#5a2a8f;
  --purple-deep:#3f1c73;
  --red:#d3122e;
  --red-deep:#b00d26;
  --ink:#1f1f24;
  --text:#3d3d44;
  --muted:#6b6b74;
  --white:#ffffff;
}
*{margin:0;padding:0;box-sizing:border-box}
html,body{width:1200px;height:3261px;overflow:hidden;background:var(--white)}
body{position:relative;font-family:"Open Sans",Arial,sans-serif;color:var(--text)}
.abs{position:absolute}
.head{font-family:"Roboto Condensed","Arial Narrow",sans-serif}

/* header */
.brand{left:160px;top:44px;font-family:"Roboto Condensed",sans-serif;font-size:34px;letter-spacing:4px;color:var(--ink);font-weight:400;line-height:36px}
.nav{top:52px;left:0;width:960px;height:20px;font-family:"Roboto Condensed",sans-serif;font-size:14px;color:var(--ink)}
.nav a{position:absolute;top:0;white-space:nowrap;color:var(--ink);text-decoration:none}
.nav a.active{color:var(--purple)}
.login{left:961px;top:43px;width:82px;height:37px;border-radius:19px;background:var(--red);color:#fff;font-family:"Roboto Condensed",sans-serif;font-weight:700;font-size:15px;display:flex;align-items:center;justify-content:center}

/* hero */
.hero-title{left:158px;top:180px;font-size:62px;line-height:72px;color:var(--ink);font-weight:400;white-space:nowrap}
.hero-title span{color:var(--purple);display:block}
.hero-list{left:160px;top:333px;list-style:none;font-family:"Roboto Condensed",sans-serif;font-size:20px;color:var(--ink);white-space:nowrap}
.hero-list li{display:flex;align-items:center;gap:10px;height:37px}
.btn{border-radius:24px;color:#fff;font-family:"Roboto Condensed",sans-serif;font-weight:700;display:flex;align-items:center;justify-content:center}
.btn-purple{background:var(--purple)}
.btn-red{background:var(--red)}
.hero-mark{left:660px;top:135px;width:390px;height:365px;display:flex;align-items:center;justify-content:center;font-family:"Roboto Condensed",sans-serif;font-size:64px;letter-spacing:6px;color:var(--ink)}

/* why */
.band{left:0;top:533px}
.why-title{left:0;width:1200px;top:695px;text-align:center;color:#fff;font-size:46px;font-weight:400}
.why-text{left:260px;width:680px;top:764px;text-align:center;color:#fff;font-size:15px;line-height:26px}
.video{left:257px;top:902px;width:686px;height:396px;border:3px solid #e8e8ee;background:linear-gradient(120deg,#6f87a8,#24324c 45%,#0f1626);box-shadow:0 22px 30px -14px rgba(0,0,0,.45)}
.play{left:570px;top:1070px}

/* products */
.section-title{left:0;width:1200px;text-align:center;color:var(--purple);font-size:46px;font-weight:400}
.product-title{font-size:36px;color:var(--ink);font-weight:400}
.product-text{font-size:14.5px;line-height:27px;text-align:justify;color:var(--text)}
.product-art{border-radius:50%;background:radial-gradient(circle at 50% 45%,#f0f0f2 0 55%,#e4e4e8 56% 100%);box-shadow:0 0 0 3px rgba(211,18,46,.85) inset}

/* join */
.join-title{left:0;width:1200px;top:2578px;text-align:center;color:#fff;font-size:38px;font-weight:400}
.join-text{left:0;width:1200px;top:2648px;text-align:center;color:#fff;font-size:31px;line-height:45px;font-weight:400}

/* footer */
.foot-brand{left:160px;top:3017px;font-family:"Roboto Condensed",sans-serif;font-size:34px;letter-spacing:4px;color:var(--ink);line-height:36px}
.social{top:3089px;width:32px;height:32px;border-radius:50%;background:var(--ink)}
.foot-head{top:2988px;font-family:"Open Sans",sans-serif;font-size:19px;color:var(--ink);font-weight:400}
.foot-list{list-style:none;font-size:14px;color:var(--ink)}
.foot-list li{height:29.5px;display:flex;align-items:center;gap:10px}
.foot-list li::before{content:"";width:0;height:0;border-left:6px solid var(--red);border-top:5px solid transparent;border-bottom:5px solid transparent}
.label{font-size:14px;color:var(--ink);font-weight:600}
.detail{font-size:12px;line-height:19px;color:var(--muted)}
.copy{left:0;width:1200px;top:3216px;text-align:center;font-size:14px;color:var(--ink)}
</style>
</head>
<body>

<header>
  <div class="abs brand">VELMORA</div>
  <nav class="abs nav" aria-label="Main">
    <a class="active" style="left:441px">Home</a>
    <a style="left:506px">About us</a>
    <a style="left:591px">KYC Product</a>
    <a style="left:696px">Loyalty Product</a>
    <a style="left:816px">Team</a>
    <a style="left:880px">Contact us</a>
  </nav>
  <div class="abs login">LOGIN</div>
</header>

<section class="hero">
  <h1 class="abs hero-title head"><span>Blockchain</span>solutions provider</h1>
  <ul class="abs hero-list">
    <li><svg width="18" height="18" viewBox="0 0 18 18"><circle cx="9" cy="9" r="9" fill="#d3122e"/><path d="M5 9.3l2.7 2.6L13 6.4" stroke="#fff" stroke-width="2.2" fill="none"/></svg>Solving problems that matter</li>
    <li><svg width="18" height="18" viewBox="0 0 18 18"><circle cx="9" cy="9" r="9" fill="#d3122e"/><path d="M5 9.3l2.7 2.6L13 6.4" stroke="#fff" stroke-width="2.2" fill="none"/></svg>Create a collaborative environment for all organisation</li>
  </ul>
  <div class="abs btn btn-purple" style="left:161px;top:437px;width:146px;height:41px;font-size:20px;font-weight:400">Contact us</div>
  <div class="abs hero-mark">VELMORA</div>
</section>

<section class="why">
  <svg class="abs band" width="1200" height="537" viewBox="0 533 1200 537" aria-hidden="true">
    <defs><linearGradient id="redFill" x1="0" y1="0" x2="1" y2="1"><stop offset="0" stop-color="#c10f29"/><stop offset=".5" stop-color="#d9173a"/><stop offset="1" stop-color="#b50c25"/></linearGradient></defs>
    <path d="M0 533 Q600 771 1200 533 V1070 H0 Z" fill="url(#redFill)"/>
  </svg>
  <h2 class="abs why-title head">Why Velmora?</h2>
  <p class="abs why-text">Velmora Technology is a technology enabler that pledges to tackle issues that have plagued organisations for years. The company is lead by a team with tremendous expertise in the field of blockchain, mobile, IT, payment and financial sector. Being a global team, the company has influence in Singapore, China , France and more.</p>
  <div class="abs video" role="img" aria-label="Video still of hands typing on a laptop with floating padlock icons"></div>
  <svg class="abs play" width="60" height="60" viewBox="0 0 60 60" aria-label="Play video"><circle cx="30" cy="30" r="30" fill="#e0102a"/><path d="M24 18 L42 30 L24 42 Z" fill="#fff"/></svg>
</section>

<section class="products">
  <h2 class="abs section-title head" style="top:1438px">Our Products</h2>

  <h3 class="abs product-title head" style="left:193px;top:1602px">KYC Product</h3>
  <p class="abs product-text" style="left:193px;top:1660px;width:446px">It is a long established fact that a reader will be distracted by the readable content of a page when looking at its layout. The point of using Lorem Ipsum is that it has a more-or-less normal distribution of letters, as opposed to using 'Content here, content here', making it look like readable English. Many desktop publishing packages and web page editors now use</p>
  <div class="abs product-art" style="left:720px;top:1566px;width:298px;height:298px" role="img" aria-label="Illustration of an identity document with profile card and red form lines"></div>

  <div class="abs product-art" style="left:210px;top:1965px;width:298px;height:298px" role="img" aria-label="Illustration of a person presenting a dashboard on a large monitor"></div>
  <h3 class="abs product-title head" style="left:563px;top:2030px">Loyalty Product</h3>
  <p class="abs product-text" style="left:563px;top:2088px;width:448px">It is a long established fact that a reader will be distracted by the readable content of a page when looking at its layout. The point of using Lorem Ipsum is that it has a more-or-less normal distribution of letters, as opposed to using 'Content here, content here', making it look like readable English. Many desktop publishing packages and web page editors now use</p>
</section>

<section class="join">
  <svg class="abs" style="left:0;top:2417px" width="1200" height="470" viewBox="0 2417 1200 470" aria-hidden="true">
    <defs><linearGradient id="purpleFill" x1="0" y1="0" x2="1" y2="1"><stop offset="0" stop-color="#4a2184"/><stop offset=".5" stop-color="#5a2a8f"/><stop offset="1" stop-color="#3f1c73"/></linearGradient></defs>
    <path d="M0 2417 Q600 2583 1200 2417 V2887 H0 Z" fill="url(#purpleFill)"/>
  </svg>
  <h2 class="abs join-title head">Do you want to be part of our teams?</h2>
  <p class="abs join-text head">Neque porro quisquam est qui dolorem ipsum<br>quia dolor sit amet, consectetur,</p>
  <div class="abs btn btn-red" style="left:493px;top:2763px;width:214px;height:48px;font-size:24px">Contact us</div>
</section>

<footer>
  <div class="abs foot-brand">VELMORA</div>
  <span class="abs social" style="left:171px"></span>
  <span class="abs social" style="left:221px;background:#d3122e"></span>
  <span class="abs social" style="left:271px"></span>
  <span class="abs social" style="left:321px"></span>

  <h4 class="abs foot-head" style="left:463px">CONTACT US</h4>
  <svg class="abs" style="left:458px;top:3036px" width="18" height="24" viewBox="0 0 18 24" aria-hidden="true"><path d="M9 1a7 7 0 0 0-7 7c0 5 7 14 7 14s7-9 7-14a7 7 0 0 0-7-7z" fill="none" stroke="#d3122e" stroke-width="1.6"/><circle cx="9" cy="8" r="2.5" fill="none" stroke="#d3122e" stroke-width="1.6"/></svg>
  <div class="abs label" style="left:487px;top:3031px">ADDRESS</div>
  <div class="abs detail" style="left:487px;top:3050px">18 Harlow Lane Brenton,<br>Northern Vale</div>
  <svg class="abs" style="left:458px;top:3101px" width="20" height="20" viewBox="0 0 20 20" aria-hidden="true"><path d="M4 2l4 4-2 3c1 2 3 4 5 5l3-2 4 4-3 3C8 18 2 12 1 5z" fill="none" stroke="#d3122e" stroke-width="1.6" stroke-linejoin="round"/></svg>
  <div class="abs label" style="left:487px;top:3101px">PHONE NUMBER</div>
  <div class="abs detail" style="left:487px;top:3123px">04 27 61 30 58</div>

  <h4 class="abs foot-head" style="left:741px">ABOUT</h4>
  <ul class="abs foot-list" style="left:741px;top:3024px"><li>Home</li><li>About Us</li><li>Services</li><li>Help us</li></ul>

  <h4 class="abs foot-head" style="left:937px">RESOURCES</h4>
  <ul class="abs foot-list" style="left:937px;top:3024px"><li>Support</li><li>Why Us</li><li>Testimonials</li><li>FAQ</li></ul>

  <p class="abs copy">© 2019 Company Name&nbsp; All right reserved</p>
</footer>

</body>
</html>
```